Redesign (8 documents) attached with brand guidelines - very quick/easy job!

We have 8 flyers/documents that we need put into the style of our new brand (see attached). So this is a simple rebrand exercise - complete with our brand guidelines (see attached)

I would need the designer to sign an NDA prior to taking this piece of work as I will be sharing newly branded documents with you prior to market release.

If these are done well we would as the same designer to work on a z-card designed brochure/POS

Brief:

- These are documents that customers would need to complete in order to book a particular service
- If you use images (ideally from Pelvano, so we don’t have to pay for them!)
- Icon ideas enclosed
-All the content on the brochures is required: but if you think it would 'flow better' in a different order that is fine.

Target Market(s)

Customers interested in receiving a particular service

Industry/Entity Type

Work

Font styles to use
Other font styles liked:
• Brandon (see brand guide)

Requirements
Must have
• A4
Nice to have
• New logo ideas
Should not have
• Anything out of brand guidleines

```html
<!DOCTYPE html>
<html lang="en">
<head>
<meta charset="utf-8">
<title>Quenvale – Health Objectives</title>
<link href="https://fonts.googleapis.com/css2?family=Open+Sans:wght@400;600;700&display=swap" rel="stylesheet">
<style>
  :root {
    --brand-blue: #1a9bc0;
    --brand-yellow: #f2e600;
    --frame-grey: #d6d8da;
    --cell-white: #ffffff;
    --text-dark: #3d3d3d;
    --text-body: #4a4a4a;
    --dots: #8a8a8a;
  }
  * { box-sizing: border-box; margin: 0; padding: 0; }
  html, body { width: 848px; height: 1200px; overflow: hidden; background: #fff; }
  body { font-family: "Open Sans", Arial, sans-serif; color: var(--text-dark); }

  .sheet { position: relative; width: 848px; height: 1200px; overflow: hidden; background: #fff; }
  .sheet-decor { position: absolute; inset: 0; }

  .brand-name {
    position: absolute; left: 52px; top: 74px;
    color: var(--brand-yellow); font-weight: 700;
    font-size: 40px; line-height: 48px;
  }

  .doc-title {
    position: absolute; right: 68px; top: 158px;
    color: var(--brand-blue); font-weight: 700; font-size: 26px; letter-spacing: 0.2px;
  }

  .field {
    position: absolute; display: flex; align-items: baseline;
    font-size: 13px; font-weight: 600; color: var(--text-dark);
  }
  .field-line { flex: 1; border-bottom: 1.5px dotted var(--dots); margin-left: 3px; height: 1px; }
  .field--nutritionist { left: 424px; width: 356px; top: 240px; }
  .field--store { left: 424px; width: 356px; top: 287px; }
  .field--client { left: 69px; width: 331px; top: 333px; }
  .field--date { left: 424px; width: 356px; top: 333px; }

  .objectives {
    position: absolute; left: 67px; top: 369px; width: 714px; height: 775px;
    background: var(--frame-grey); border-radius: 14px; padding: 8px;
    display: flex; flex-direction: column; gap: 8px;
  }
  .reason { display: flex; flex-direction: column; gap: 3px; }
  .reason-head {
    display: grid; grid-template-columns: 250px 1fr; height: 28px; align-items: center;
    background: var(--brand-blue); color: #fff; font-weight: 700; font-size: 14px;
    border-radius: 10px 10px 0 0;
  }
  .reason-head span:first-child { padding-left: 13px; }
  .reason-head span:last-child { padding-left: 8px; }
  .reason-row { display: grid; grid-template-columns: 246px 1fr; gap: 3px; height: 83px; }
  .prompt, .answer { background: var(--cell-white); border-radius: 10px; }
  .prompt {
    display: flex; align-items: center; padding: 0 26px 0 14px;
    font-size: 10.5px; line-height: 15px; color: var(--text-body);
  }
</style>
</head>
<body>
<div class="sheet">
  <svg class="sheet-decor" width="848" height="1200" viewBox="0 0 848 1200" aria-hidden="true">
    <path d="M0 0 H848 V40 C560 60 260 150 0 290 Z" fill="var(--brand-blue)"/>
    <path d="M0 290 C260 150 560 60 848 40" fill="none" stroke="var(--brand-yellow)" stroke-width="8"/>
    <path d="M848 1120 C740 1170 620 1192 470 1200 H848 Z" fill="var(--brand-blue)"/>
  </svg>

  <div class="brand-name">Quenvale</div>

  <h1 class="doc-title">HEALTH OBJECTIVES</h1>

  <div class="field field--nutritionist">Nutritionist’s name:<span class="field-line"></span></div>
  <div class="field field--store">Store location:<span class="field-line"></span></div>
  <div class="field field--client">Client’s name:<span class="field-line"></span></div>
  <div class="field field--date">Date of consultation:<span class="field-line"></span></div>

  <div class="objectives">
    <section class="reason">
      <div class="reason-head"><span>Reason 1</span><span>Your comments</span></div>
      <div class="reason-row"><div class="prompt">Symptom, issue or condition you want to address.</div><div class="answer"></div></div>
      <div class="reason-row"><div class="prompt">Duration - how long have you felt like this or experienced this symptom(s)?</div><div class="answer"></div></div>
      <div class="reason-row"><div class="prompt">Have you seen a doctor about this for a diagnosis? Did you receive any medical treatment?</div><div class="answer"></div></div>
      <div class="reason-row"><div class="prompt">Is there any background or extra health or lifestyle information that relates to this situation that you want your practitioner to know about? Please give details.</div><div class="answer"></div></div>
    </section>
    <section class="reason">
      <div class="reason-head"><span>Reason 2</span><span>Your comments</span></div>
      <div class="reason-row"><div class="prompt">Symptom, issue or condition you want to address.</div><div class="answer"></div></div>
      <div class="reason-row"><div class="prompt">Duration - how long have you felt like this or experienced this symptom(s)?</div><div class="answer"></div></div>
      <div class="reason-row"><div class="prompt">Have you seen a doctor about this for a diagnosis? Did you receive any medical treatment?</div><div class="answer"></div></div>
      <div class="reason-row"><div class="prompt">Is there any background or extra health or lifestyle information that relates to this situation that you want your practitioner to know about? Please give details.</div><div class="answer"></div></div>
    </section>
  </div>
</div>
</body>
</html>
```